Law Offices business card

Hi there, I'll need business card for the Law Offices of Colin Matheny. The information must convey his strategic approach and quick resolution to complex business litigation needs. Please emphasize Civil Litigation, Corporate Law, Business Governance and Real Estate Law. Colin has over 25 years of experience in these fields.The card should be modern and edgy and the message should be clear. Please consult his current website for ideas.

```html
<!DOCTYPE html>
<html lang="en">
<head>
<meta charset="utf-8">
<title>Law Offices of Colin Matheny – Business Card</title>
<link rel="stylesheet" href="https://fonts.googleapis.com/css2?family=Open+Sans:wght@400;600;700&display=swap">
<style>
  :root {
    --backdrop: #2b2b2d;
    --card: #ffffff;
    --ink: #1c1c1c;
    --ink-soft: #3a3a3a;
    --accent: #d42a2a;
    --rule: #8a8a8a;
  }
  * { box-sizing: border-box; margin: 0; padding: 0; }
  html, body {
    width: 1200px; height: 900px; overflow: hidden;
    background: var(--backdrop);
    font-family: "Open Sans", Arial, sans-serif;
    color: var(--ink);
  }
  .stage { position: relative; width: 1200px; height: 900px; }

  .card {
    position: absolute;
    width: 700px; height: 400px;
    background: var(--card);
    border-radius: 22px;
    box-shadow: 0 18px 40px rgba(0,0,0,.45);
    overflow: hidden;
  }
  .card--front { left: 120px; top: 40px; }
  .card--back  { left: 380px; top: 460px; }

  /* firm name block */
  .firm {
    position: absolute;
    display: flex; align-items: flex-start; gap: 16px;
  }
  .firm__square {
    width: 22px; height: 22px; margin-top: 8px;
    background: var(--accent);
    flex: none;
  }
  .firm__name {
    font-weight: 700; color: var(--ink);
    line-height: 1.08; letter-spacing: .5px;
    white-space: nowrap;
  }
  .firm__prefix { display: block; font-size: 20px; text-transform: uppercase; letter-spacing: 2px; }
  .firm__main { display: block; font-size: 46px; }

  .card--front .firm { left: 150px; top: 90px; }

  .services {
    position: absolute; left: 380px; top: 215px;
    list-style: none;
    font-size: 15px; letter-spacing: .8px; line-height: 1.5;
    text-transform: uppercase; color: var(--ink-soft);
  }
  .services .is-accent { color: var(--accent); }
  .services__experience {
    margin-top: 8px; font-weight: 600; color: var(--ink);
  }

  /* back */
  .card--back .firm { left: 50px; top: 225px; gap: 12px; }
  .card--back .firm__square { width: 18px; height: 18px; margin-top: 6px; }
  .card--back .firm__prefix { font-size: 15px; }
  .card--back .firm__main { font-size: 30px; }

  .divider {
    position: absolute; left: 420px; top: 60px;
    width: 2px; height: 220px;
    background: linear-gradient(var(--rule), rgba(138,138,138,0));
  }
  .contact { position: absolute; left: 445px; top: 58px; }
  .contact__name { font-size: 24px; font-weight: 700; letter-spacing: .5px; text-transform: uppercase; }
  .contact__role { font-size: 13px; font-weight: 600; color: var(--accent); letter-spacing: 1px; text-transform: uppercase; margin-bottom: 10px; }
  .contact__address { font-style: normal; font-size: 15px; line-height: 1.3; color: var(--ink-soft); margin-bottom: 10px; }
  .contact__list { list-style: none; font-size: 15px; line-height: 1.45; color: var(--ink-soft); }
  .contact__list li { display: flex; align-items: center; gap: 10px; }
  .contact__list svg { width: 13px; height: 13px; fill: var(--accent); flex: none; }
</style>
</head>
<body>
<main class="stage">

  <section class="card card--front" aria-label="Business card front">
    <div class="firm">
      <span class="firm__square"></span>
      <p class="firm__name">
        <span class="firm__prefix">Law Offices of</span>
        <span class="firm__main">Colin Matheny, PA</span>
      </p>
    </div>
    <ul class="services">
      <li>Civil Litigation</li>
      <li>Corporate Law</li>
      <li>Business Governance</li>
      <li class="is-accent">Real Estate Law</li>
      <li class="services__experience">Over 25 Years of Experience</li>
    </ul>
  </section>

  <section class="card card--back" aria-label="Business card back">
    <div class="firm">
      <span class="firm__square"></span>
      <p class="firm__name">
        <span class="firm__prefix">Law Offices of</span>
        <span class="firm__main">Colin Matheny, PA</span>
      </p>
    </div>

    <span class="divider"></span>

    <div class="contact">
      <h1 class="contact__name">Colin Matheny</h1>
      <p class="contact__role">Attorney</p>
      <address class="contact__address">118B Harbor Lane<br>Coral Point, FL 33911</address>
      <ul class="contact__list">
        <li>
          <svg viewBox="0 0 24 24"><path d="M6.6 10.8a15.1 15.1 0 0 0 6.6 6.6l2.2-2.2a1 1 0 0 1 1-.25 11.4 11.4 0 0 0 3.6.57 1 1 0 0 1 1 1V20a1 1 0 0 1-1 1A17 17 0 0 1 3 4a1 1 0 0 1 1-1h3.5a1 1 0 0 1 1 1c0 1.25.2 2.45.57 3.570a1 1 0 0 1-.25 1z"/></svg>
          555-204-7183
        </li>
        <li>
          <svg viewBox="0 0 24 24"><path d="M6 2h12v6H6zM4 9h16a2 2 0 0 1 2 2v7h-4v4H6v-4H2v-7a2 2 0 0 1 2-2zm4 8v3h8v-3z"/></svg>
          555-310-6642
        </li>
        <li>
          <svg viewBox="0 0 24 24"><path d="M2 5h20v14H2zm2 2v.5l8 5 8-5V7zm0 2.9V17h16V9.9l-8 5z"/></svg>
          colin@mathenylaw.com
        </li>
        <li>
          <svg viewBox="0 0 24 24"><path d="M12 2a10 10 0 1 0 0 20 10 10 0 0 0 0-20zm6.9 9h-3a15 15 0 0 0-1.3-5.6A8 8 0 0 1 18.9 11zM12 4.1c.9 1.2 1.7 3.6 1.9 6.9h-3.8c.2-3.3 1-5.7 1.9-6.9zM9.4 5.4A15 15 0 0 0 8.1 11h-3a8 8 0 0 1 4.3-5.6zM5.1 13h3a15 15 0 0 0 1.3 5.6A8 8 0 0 1 5.1 13zm6.9 6.9c-.9-1.200-1.7-3.6-1.9-6.9h3.8c-.2 3.3-1 5.7-1.9 6.9zm2.6-1.3a15 15 0 0 0 1.3-5.6h3a8 8 0 0 1-4.3 5.6z"/></svg>
          www.mathenylaw.com
        </li>
      </ul>
    </div>
  </section>

</main>
</body>
</html>
```